Printing Company needs Website

PLEASE REVIEW ALL IMAGES, I HAVE INCLUDED A WEBSITE MOCKUP IDEA AND LOGO FILES IN THESE IMAGES.

Vel-Marks Provides printing services to multiple businesses. We Focus on 4 main markets. Signage (Signs, Banners, Wraps, Custom graphics), Printing (flyers, brochures, business cards, Postcards), Apparel (printed shirts, hoodies, sweatshirts), Promotional Products (mugs, golf balls, brava cans, pens), We try to sell ourselves on total brand imaging, our slogan is "Mark Everything." because we want to be able to provide any type of printing to our customers. Consumer targeting should be targeted towards small business, and wholesale targeting should be geared toward, merchandising, branding, marketing, design, signage, apparel, embroidery, and printing groups. WE DO OFFER DESIGN SERVICES, I have attached one orlwick guild logo design as an example.

I need a website designed both for wholesale and consumer based people. Wholesale customers would have their own login and consumers would also have their own.
I need there to be an online designer software (possibly java) built in so that the customer can order their product or upload their artwork online to see the proof for approval. There will need to be an commence setup, and I do have a quillpay account if that helps. Shipping must be auto calculated at the time of ordering. I would Like to make it to where when customer orders a product if it is outside of the dimensions requested on the site that the customer is warned of clipping or skewing.

I will be working closely aside the designer I pick to aid in the uploading and configuration of pricing structure, weight, and imagery if selected. This will be a lengthy project, and I will be willing to pay for the additional help so long as you are completely aware of the needs, Happy designing!!
Updates

I love all of the designs so far everyone! I will be reviewing PLEASE NOTE, IF I APPROVE YOUR WEB DESIGN, I WILL WANT YOU TO COMPLETE THE ENTIRE DESIGN INCLUDING A DESIGN PROOFING SETUP FOR MY CUSTOMERS INTEGRATED IN AS I HAVE STATED IN THE ORIGINAL STATEMENT. PLEASE ASK QUESTIONS IF YOU DON'T UNDERSTAND!

Target Market(s)

Small Business, School Athletics, Merchandising groups, Branding Groups, Larger Printers, Sign makers, Embroidery shops, Screen Printing Shops

Industry/Entity Type

It Company

Font styles to use
Sans Serif

Colors
000000
1b1b1b
757575
ec1f27

Requirements
Must have
• Built in design setup to each product with sizing, Ability to add pre-designed templates, .pdf print ready files after upload, Wholesale account, or Business accounts all with different pricing structures, Must be willing to aid in setup of all products and services (willing pay additional for setup costs.)
Nice to have
• SEO Optimization, targeting specific groups listed, automatic ordering to outsource vendors straight from site listing drop ship location if need be.

```html
<!DOCTYPE html>
<html lang="en">
<head>
<meta charset="utf-8">
<title>Vel-Marks — Mark Everything.</title>
<link rel="stylesheet" href="https://fonts.googleapis.com/css2?family=Montserrat:wght@400;700&family=Open+Sans:wght@400;600&display=swap">
<style>
  :root {
    --red: #ec1f27;
    --black: #000000;
    --ink: #1b1b1b;
    --grey: #757575;
    --panel: #23262c;
    --panel-edge: #3b3f47;
    --footer: #141414;
    --white: #ffffff;
    --muted: #c9c9c9;
  }
  * { box-sizing: border-box; margin: 0; padding: 0; }
  html, body { width: 1200px; height: 581px; overflow: hidden; background: var(--black); }
  body { font-family: "Open Sans", Arial, sans-serif; color: var(--white); position: relative; }

  .hero { position: absolute; left: 0; top: 0; width: 1200px; height: 509px; overflow: hidden; }
  .hero-photo {
    position: absolute; inset: 0;
    background:
      linear-gradient(90deg, rgba(20,10,10,.55) 0%, rgba(0,0,0,0) 30%, rgba(0,0,0,0) 80%, rgba(60,30,25,.5) 100%),
      linear-gradient(180deg, #3a2a2a 0%, #8e2a30 22%, #7a5a5e 45%, #9a9ea4 62%, #6c6a68 80%, #4c4846 100%);
    filter: saturate(.9);
  }
  .hero-photo::after { content: ""; position: absolute; inset: 0; background: rgba(0,0,0,.18); }

  .site-header {
    position: absolute; left: 0; top: 0; width: 1200px; height: 84px;
    background: rgba(20,8,10,.55);
  }
  .brand { position: absolute; left: 231px; top: 22px; display: flex; align-items: center; gap: 8px; }
  .brand-dot { width: 26px; height: 26px; border-radius: 50%; background: var(--red); }
  .brand-text { display: flex; flex-direction: column; }
  .brand-name { font-family: "Montserrat", Arial, sans-serif; font-weight: 700; font-size: 22px; line-height: 24px; color: var(--white); }
  .brand-tag { font-family: "Montserrat", Arial, sans-serif; font-weight: 700; font-size: 7px; color: var(--white); align-self: flex-end; }

  .main-nav { position: absolute; left: 469px; top: 0; height: 84px; display: flex; gap: 0; }
  .main-nav a {
    display: block; height: 84px; line-height: 86px; padding: 0 11.5px;
    font-size: 10px; font-weight: 600; color: var(--white); text-decoration: none; letter-spacing: .1px;
  }
  .main-nav a:first-child { padding-left: 0; }
  .main-nav a.is-active { color: var(--red); box-shadow: inset 0 -2px 0 var(--red); }

  .slide-arrow {
    position: absolute; top: 232px; width: 22px; height: 57px;
    background: rgba(255,255,255,.25); display: flex; align-items: center; justify-content: center;
  }
  .slide-arrow.prev { left: 12px; }
  .slide-arrow.next { left: 1166px; }

  .hero-title {
    position: absolute; left: 230px; top: 261px; height: 39px; padding: 0 13px 0 8px;
    background: rgba(60,60,62,.78);
    font-family: "Montserrat", Arial, sans-serif; font-size: 32px; line-height: 39px; color: var(--white); letter-spacing: .5px;
  }
  .hero-actions { position: absolute; left: 230px; top: 311px; display: flex; gap: 11px; }
  .btn {
    height: 30px; line-height: 28px; padding: 0 20px; font-size: 7.5px; font-weight: 600;
    letter-spacing: .6px; text-decoration: none; color: var(--white); border: 1.5px solid transparent;
  }
  .btn-primary { background: var(--red); border-color: var(--red); }
  .btn-outline { border-color: var(--white); color: var(--muted); }

  .pager { position: absolute; left: 232px; top: 467px; display: flex; align-items: center; gap: 6px; font-size: 11px; }

  .services { position: absolute; left: 672px; top: 131px; }
  .service-title { font-family: "Open Sans", Arial, sans-serif; font-size: 16px; fill: var(--white); letter-spacing: .3px; }
  .service-desc { font-family: "Open Sans", Arial, sans-serif; font-size: 9.5px; fill: #b9bcc2; }

  .site-footer { position: absolute; left: 0; top: 509px; width: 1200px; height: 72px; background: var(--footer); }
  .copyright { position: absolute; left: 230px; top: 19px; font-size: 9px; color: var(--white); }
  .footer-nav { position: absolute; left: 230px; top: 41px; font-size: 8px; color: var(--white); display: flex; }
  .footer-nav a { color: var(--white); text-decoration: none; }
  .footer-nav span { padding: 0 9px; }
  .social { position: absolute; left: 812px; top: 20px; display: flex; gap: 4.5px; }
  .social-link { width: 28px; height: 28px; border-radius: 50%; background: #3d3d3d; display: block; }
</style>
</head>
<body>
  <section class="hero">
    <div class="hero-photo" role="img" aria-label="Blurred photo of a storefront with red printed window signage and a parking lot reflected in the glass"></div>

    <header class="site-header">
      <div class="brand">
        <span class="brand-dot"></span>
        <div class="brand-text">
          <span class="brand-name">Vel-Marks</span>
          <span class="brand-tag">Mark Everything.</span>
        </div>
      </div>
      <nav class="main-nav">
        <a href="#" class="is-active">HOME</a>
        <a href="#">SIGNAGE</a>
        <a href="#">PRINTING</a>
        <a href="#">DESIGN</a>
        <a href="#">PROMOTIONAL</a>
        <a href="#">APPAREL</a>
        <a href="#">ABOUT US</a>
        <a href="#">CONTACT US</a>
      </nav>
    </header>

    <a class="slide-arrow prev" href="#" aria-label="Previous slide">
      <svg width="8" height="10" viewBox="0 0 8 10"><path d="M6 1 2 5l4 4" fill="none" stroke="#fff" stroke-width="1.4"/></svg>
    </a>
    <a class="slide-arrow next" href="#" aria-label="Next slide">
      <svg width="8" height="10" viewBox="0 0 8 10"><path d="M2 1l4 4-4 4" fill="none" stroke="#fff" stroke-width="1.4"/></svg>
    </a>

    <h1 class="hero-title">Mark Everything</h1>
    <div class="hero-actions">
      <a class="btn btn-primary" href="#">READ MORE</a>
      <a class="btn btn-outline" href="#">CONTACT NOW</a>
    </div>

    <div class="pager">
      <svg width="12" height="13" viewBox="0 0 12 13"><path d="M11 1 1.5 6.5 11 12Z" fill="none" stroke="#fff" stroke-width="1.2"/></svg>
      <span>1/3</span>
      <svg width="12" height="13" viewBox="0 0 12 13"><path d="M1 1l9.5 5.5L1 12Z" fill="none" stroke="#ec1f27" stroke-width="1.4"/></svg>
    </div>

    <svg class="services" width="292" height="330" viewBox="0 0 292 330">
      <!-- Signage -->
      <g class="service">
        <polygon points="24,0 288,0 261,79 0,79" fill="var(--panel)" stroke="var(--panel-edge)" stroke-width="2"/>
        <polygon points="27,4 121,4 99,75 5,75" fill="var(--red)"/>
        <g fill="#fff">
          <rect x="47" y="32" width="30" height="13"/>
          <polygon points="40,37 50,37 50,52 40,52 44,44.5"/>
          <polygon points="84,37 74,37 74,52 84,52 80,44.5"/>
        </g>
        <text class="service-title" x="126" y="24">SIGNAGE</text>
        <text class="service-desc" x="112" y="47">Signs, Banners, Wraps,</text>
        <text class="service-desc" x="112" y="60">Custom graphics</text>
      </g>
      <!-- Printing -->
      <g class="service">
        <polygon points="0,83 261,83 288,161 24,161" fill="var(--panel)" stroke="var(--panel-edge)" stroke-width="2"/>
        <polygon points="167,87 258,87 284,157 193,157" fill="var(--red)"/>
        <g fill="#fff">
          <rect x="215" y="107" width="18" height="6"/>
          <rect x="209" y="114" width="30" height="14" rx="3"/>
          <rect x="215" y="124" width="18" height="10" fill="#fff" stroke="var(--red)" stroke-width="1.5"/>
        </g>
        <text class="service-title" x="162" y="106" text-anchor="end">PRINTING</text>
        <text class="service-desc" x="174" y="127" text-anchor="end">flyers, brochures, business</text>
        <text class="service-desc" x="174" y="140" text-anchor="end">cards, Postcards</text>
      </g>
      <!-- Apparel -->
      <g class="service">
        <polygon points="24,165 288,165 261,244 0,244" fill="var(--panel)" stroke="var(--panel-edge)" stroke-width="2"/>
        <polygon points="27,169 121,169 99,240 5,240" fill="var(--red)"/>
        <path d="M55 191 l-11 5 4 9 5-2 v17 h18 v-17 l5 2 4-9 -11-5 c-2 4-12 4-14 0z" fill="#fff"/>
        <text class="service-title" x="126" y="189">APPAREL</text>
        <text class="service-desc" x="112" y="211">printed shirts, hoodies,</text>
        <text class="service-desc" x="112" y="224">sweatshirts</text>
      </g>
      <!-- Promotional products -->
      <g class="service">
        <polygon points="0,248 261,248 288,326 24,326" fill="var(--panel)" stroke="var(--panel-edge)" stroke-width="2"/>
        <polygon points="167,252 258,252 284,322 193,322" fill="var(--red)"/>
        <g fill="none" stroke="#fff" stroke-width="2.5">
          <path d="M212 275 h22 v12 a11 10 0 0 1 -22 0 z" fill="#fff"/>
          <path d="M212 279 h-3 v8 a6 6 0 0 0 6 5"/>
        </g>
        <text class="service-title" x="162" y="264" text-anchor="end">PROMOTIONAL</text>
        <text class="service-title" x="162" y="280" text-anchor="end">PRODUCTS</text>
        <text class="service-desc" x="174" y="298" text-anchor="end">mugs, golf balls, brava cans,</text>
        <text class="service-desc" x="174" y="311" text-anchor="end">pens</text>
      </g>
    </svg>
  </section>

  <footer class="site-footer">
    <p class="copyright">Copyright(c) 2016 website name, All Rights Reserved.</p>
    <nav class="footer-nav">
      <a href="#">HOME</a><span>|</span>
      <a href="#">Signage</a><span>|</span>
      <a href="#">Printing</a><span>|</span>
      <a href="#">Design</a><span>|</span>
      <a href="#">Promotional</a><span>|</span>
      <a href="#">Apparel</a><span>|</span>
      <a href="#">About Us</a><span>|</span>
      <a href="#">Contact Us</a>
    </nav>
    <div class="social">
      <a class="social-link" href="#" aria-label="Social profile 1"></a>
      <a class="social-link" href="#" aria-label="Social profile 2"></a>
      <a class="social-link" href="#" aria-label="Social profile 3"></a>
      <a class="social-link" href="#" aria-label="Social profile 4"></a>
      <a class="social-link" href="#" aria-label="Social profile 5"></a>
    </div>
  </footer>
</body>
</html>
```